sydney wedding photography business needs a business card design

we need a business card design for a sydney based wedding photography and videography business. our business name is :golden hour studio and film. our target clients are 24-35 yrs female. our style is candid, organic, natural, dynamic. we are a team of young photographers and videographers, and help brides to create memories that they will cherish for the rest of their lives. the logo will be provided. we want an elegant design that reflects our style, and also want to give a great impression to our clients that we are one of the best studios in sydney and our brand means quality and premium service.

Target Market(s)

bride to be, 24-35 years old, living in sydney and surrunding areas

Industry/Entity Type

Wedding Photography

Contact Information for Business Card

address: 57 tarrant street, glenmore nsw 2047
mobile: 0431872259
phone: (02) 9163 2408
info@tidewillowstudio.net.au
www.tidewillowstudio.net.au
facebook:tidewillowweddings
instagram:tidewillowweddings

Font styles to use
Serif
Sans Serif

Requirements
Nice to have
• maybe add my slogan"memories beyond eternity" if the layout looks good
Should not have
• no black color, not good idea for wedding biz card

```html
<!DOCTYPE html>
<html lang="en">
<head>
<meta charset="utf-8">
<title>Golden Hour Studio and Film – Business Card</title>
<link href="https://fonts.googleapis.com/css2?family=Raleway:wght@300;400;500&display=swap" rel="stylesheet">
<style>
  :root {
    --page-bg: #3a3a3c;
    --card-espresso: #3b2a1e;
    --card-espresso-light: #4a3526;
    --gold-light: #f0b81c;
    --gold-mid: #d19410;
    --gold-deep: #a8690c;
    --gold-text: #e0a52a;
    --ink-cream: #f3ead9;
  }
  html, body {
    margin: 0;
    padding: 0;
    width: 1200px;
    height: 1200px;
    overflow: hidden;
    background: var(--page-bg);
    font-family: "Raleway", sans-serif;
  }
  .canvas {
    width: 1200px;
    height: 1200px;
    display: flex;
    flex-direction: column;
    align-items: center;
    justify-content: center;
    gap: 56px;
  }
  .card {
    position: relative;
    width: 840px;
    height: 480px;
    box-sizing: border-box;
    padding: 20px;
    background: linear-gradient(135deg, var(--gold-light) 0%, var(--gold-mid) 45%, var(--gold-deep) 75%, var(--gold-mid) 100%);
    box-shadow: 0 10px 30px rgba(0,0,0,0.45);
  }
  .card-face {
    position: relative;
    width: 100%;
    height: 100%;
    background: var(--card-espresso);
    overflow: hidden;
  }
  .brand-name {
    position: absolute;
    left: 0;
    right: 0;
    margin: 0;
    text-align: center;
    color: var(--gold-text);
    font-weight: 400;
    letter-spacing: 0.04em;
    white-space: nowrap;
  }
  .card-front .brand-name { top: 86px; font-size: 40px; }
  .location {
    position: absolute;
    top: 190px;
    left: 70px;
    width: 220px;
    text-align: right;
    color: var(--ink-cream);
    font-size: 18px;
    font-weight: 300;
    line-height: 1.35;
  }
  .person {
    position: absolute;
    top: 188px;
    left: 410px;
    text-align: center;
  }
  .person-name {
    margin: 0;
    color: var(--gold-text);
    font-size: 32px;
    font-weight: 400;
    letter-spacing: 0.01em;
  }
  .person-role {
    margin: 4px 0 0;
    color: var(--ink-cream);
    font-size: 17px;
    font-weight: 300;
  }
  .phone, .online {
    position: absolute;
    bottom: 70px;
    color: var(--ink-cream);
    font-size: 18px;
    font-weight: 300;
    line-height: 1.4;
  }
  .phone { left: 200px; }
  .online { right: 70px; }
  .back-pattern {
    position: absolute;
    inset: 0;
    background: radial-gradient(ellipse at 50% 40%, var(--card-espresso-light) 0%, var(--card-espresso) 75%);
  }
  .card-back .brand-name { top: 190px; font-size: 50px; }
</style>
</head>
<body>
<main class="canvas">
  <section class="card card-front" aria-label="Business card front">
    <div class="card-face">
      <h1 class="brand-name">Golden Hour Studio and Film</h1>
      <div class="location">57 Tarrant Street<br>Glenmore NSW 2047</div>
      <div class="person">
        <p class="person-name">JOHN DOE</p>
        <p class="person-role">Director</p>
      </div>
      <div class="phone">Tel:&nbsp; (02) 9163 2408<br>Mob: 0431 872 259</div>
      <div class="online">www.tidewillowstudio.net.au<br>info@tidewillowstudio.net.au</div>
    </div>
  </section>

  <section class="card card-back" aria-label="Business card back">
    <div class="card-face">
      <div class="back-pattern" role="img" aria-label="Faint warm checkered background texture"></div>
      <h2 class="brand-name">Golden Hour Studio and Film</h2>
    </div>
  </section>
</main>
</body>
</html>
```